"Copper Lantern" Play - Poster Design for Theatre Group

We are an amateur theatre group based in Geneva, Switzerland. We take pride in eye-catching posters for our shows, which are printed in various sizes.
This design will be for a play in March 2016. The play is called "Copper Lantern", and it's a Marwick Medal winner from Martin Crowe-Fenwick. The play is about a couple who have everything a family could want, until they lose a child in a life-shattering accident that turns their world upside down. The play charts the couple's bittersweet search to find each other and to find comfort.
Most importantly, we want a design that will make people want to see the show. We don't want to give away the plot or be too heavy-handed about death, but we want it to be clear that it's not a comedy (although there are some lighter moments!).
Attached you will find a template for the poster. This simply has our group name and logo in the top right corner: (Lakeside Stage Players Guild presents).
You may change the color of both the text and the logo, but please do not change the font, size, or location.
Here is the information that needs to be on the poster, wherever you see fit:
play title: Copper Lantern
author byline: by Martin Crowe-Fenwick
director line: directed by Ned Pilbury
tagline: How do you keep it together when your whole world's fallen apart?
dates and times:
1-5 March 2016
(Tue-Fri 20:00, Sat 19:00)
location:
Théâtre du Colibri
Eaux-Vives, Geneva
websites:
www.lspg.ch
www.scenesansfrontiere.ch
Technical Details:
Any font or combination of fonts is acceptable. The largest text should be the play title. The author's name must be at least 50% of the title font size.
For this competition, we would like the version with A3 proportions, which will also be used at F4 (89.5 x 128 cm) and A5 sizes (14.8 x 21 cm). Therefore no text should be below 9pt at A5.
However, from the winning designer we will also need repurposed sizes of the same design. Here is a comprehensive list of the sizes we will need.
1) A3 print poster. Artwork should be 300dpi, CMYK, sent with a 1mm bleed all round, to specification PDF/X-1A:2001. We will need this image in PDF format in addition to the default Artmarketo formats.
2) Chatterbook advert picture. 1200px by 628px, RGB jpeg. This must comply with Chatterbook’s restrictions on amount of text, which is no more than 20% of area taken up by text.(https://www.chatterbook-example.com/ads/tools/text_overlay).
Because of these restrictions it is sufficient to include just the title and the author's name in this version.
3) Chatterbook cover picture: 851px by 314px. RGB jpeg. It is sufficient to include just the title and the author's name in this version.
4) Web banner. 1000px by 300px. RGB jpeg. This version should include just the main image(s), no text.

```html
<!DOCTYPE html>
<html lang="en">
<head>
<meta charset="utf-8">
<title>Copper Lantern – Lakeside Stage Players Guild</title>
<link rel="stylesheet" href="https://fonts.googleapis.com/css2?family=Arimo:wght@400;700&family=Caveat+Brush&display=swap">
<style>
  :root {
    --ink: #ffffff;
    --night: #050506;
    --tunnel: #4a4a4c;
    --tunnel-mid: #232325;
    --glow: #d9c9a6;
    --glow-warm: #8a7350;
  }
  * { margin: 0; padding: 0; box-sizing: border-box; }
  html, body { width: 865px; height: 1200px; overflow: hidden; background: var(--night); }
  .poster {
    position: relative;
    width: 865px;
    height: 1200px;
    overflow: hidden;
    color: var(--ink);
    font-family: "Arimo", Arial, sans-serif;
    background: var(--night);
  }
  .scene-photo {
    position: absolute;
    inset: 0;
    background:
      radial-gradient(ellipse 80px 110px at 432px 870px, var(--glow) 0%, var(--glow-warm) 45%, transparent 100%),
      radial-gradient(ellipse 340px 430px at 432px 720px, var(--tunnel) 0%, var(--tunnel-mid) 55%, transparent 100%),
      radial-gradient(ellipse 520px 640px at 432px 640px, #2c2c2e 0%, #121213 60%, var(--night) 100%);
  }
  .presenter {
    position: absolute;
    top: 16px;
    right: 14px;
    display: flex;
    align-items: center;
    gap: 10px;
  }
  .presenter-name {
    text-align: right;
    font-weight: 700;
    font-size: 17px;
    line-height: 1.15;
    width: 130px;
  }
  .presenter-mark {
    width: 96px;
    height: 96px;
    border-radius: 50%;
    background: var(--ink);
  }
  .title {
    position: absolute;
    left: 160px;
    top: 200px;
    font-family: "Caveat Brush", cursive;
    font-weight: 400;
    font-size: 108px;
    line-height: 1;
    text-transform: lowercase;
  }
  .byline {
    position: absolute;
    left: 165px;
    top: 333px;
    font-weight: 700;
    font-size: 40px;
    letter-spacing: -0.3px;
  }
  .director {
    position: absolute;
    left: 395px;
    top: 392px;
    font-weight: 700;
    font-size: 22px;
  }
  .tagline {
    position: absolute;
    left: 265px;
    top: 442px;
    width: 520px;
    font-size: 25px;
    line-height: 1.6;
  }
  .dates {
    position: absolute;
    left: 43px;
    top: 1036px;
    font-weight: 700;
    font-size: 50px;
    line-height: 1;
  }
  .times {
    position: absolute;
    right: 30px;
    top: 1048px;
    font-weight: 700;
    font-size: 33px;
    line-height: 1;
  }
  .venue {
    position: absolute;
    left: 52px;
    top: 1124px;
    font-weight: 700;
    font-size: 20px;
    line-height: 1;
  }
  .websites {
    position: absolute;
    right: 30px;
    top: 1100px;
    text-align: right;
    font-weight: 700;
    font-size: 17px;
    line-height: 1.4;
  }
</style>
</head>
<body>
  <main class="poster">
    <div class="scene-photo" role="img" aria-label="Dark tunnel photograph with the silhouettes of a man and a woman facing each other, and a small child standing in the light at the tunnel's end"></div>

    <header class="presenter">
      <p class="presenter-name">Lakeside Stage Players Guild presents</p>
      <span class="presenter-mark" aria-hidden="true"></span>
    </header>

    <h1 class="title">copper lantern</h1>
    <p class="byline">by Martin Crowe-Fenwick</p>
    <p class="director">directed by Ned Pilbury</p>
    <p class="tagline">How do you keep it together<br>when your whole world's fallen apart?</p>

    <p class="dates">1-5 March 2016</p>
    <p class="times">Tue-Fri 20:00, Sat 19:00</p>
    <p class="venue">Théâtre du Colibri Eaux-Vives, Geneva</p>
    <p class="websites">www.lspg.ch<br>www.scenesansfrontiere.ch</p>
  </main>
</body>
</html>
```